Design the Business card for NetVaultic

Business card required for a professional Cyber Security business.
Company Logo and Icon has already been provided however I would like other options for the logo and icon to compare to. Alternatively, please refine/enhance the image of the logo.icon I have already provided.

If you are going to use the provided logo and icon, I was thinking that the company raised Logo on White background would serve well on the front of the card. See attached. AND, a large company raised stand-alone icon to appear on black background on the back of the card with tagline 'Cyber Risk Management, Governance and Consulting' or 'Cyber Security for your Business' See attached.
Alternatively, provide your own design for the logo and icon.

Target Market(s)

Enterprise, Government, Financial.

Contact Information for Business Card

Tavin Orloweth
Founder and CEO

Email Address
Mobile Number
Website URL
LinkedIn URL

Logo Text

NetVaultic - see attached example of logo

Font styles to use
Other font styles liked:
• Berlin Sans FB

Requirements
Must have
• Clean large and bold icon on the back with tagline.
• Horizontal alignment,
Nice to have
• Round edges.
• Raised Logo/Icon
Should not have
• An unprofessional look and feel.

```html
<!DOCTYPE html>
<html lang="en">
<head>
<meta charset="utf-8">
<title>NetVaultic Business Card</title>
<link rel="stylesheet" href="https://fonts.googleapis.com/css2?family=Roboto:wght@400;500&family=Roboto+Condensed:wght@700&family=Ubuntu:wght@500&display=swap">
<style>
  :root {
    --backdrop: #2b2b2c;
    --card-light: #f3f3f3;
    --card-dark: #1c1d1f;
    --brand-blue: #1a6fc4;
    --band-blue: #4a72c4;
    --brand-yellow: #f5b800;
    --text-gray: #4a4a4a;
    --divider: #cfcfcf;
  }
  * { margin: 0; padding: 0; box-sizing: border-box; }
  html, body { width: 1200px; height: 960px; overflow: hidden; }
  body { background: var(--backdrop); position: relative; font-family: "Roboto", Arial, sans-serif; }

  .card { position: absolute; left: 322px; width: 599px; height: 342px; border-radius: 16px; overflow: hidden; }
  .card-front { top: 108px; background: var(--card-light); }
  .card-back { top: 494px; background: var(--card-dark); }

  .front-wordmark { position: absolute; left: 393px; top: 246px; display: flex; align-items: center; gap: 10px; }
  .front-wordmark, .contact-block, .divider, .back-wordmark, .tagline, .footer-bands { /* positioned relative to card */ }

  .brand-dot { width: 52px; height: 52px; border-radius: 50%; background: var(--band-blue); }
  .brand-name { font-family: "Ubuntu", Arial, sans-serif; font-weight: 500; font-size: 36px; color: var(--brand-blue); line-height: 1; }

  .divider { position: absolute; left: 331px; top: 102px; width: 1px; height: 146px; background: var(--divider); }

  .contact-block { position: absolute; left: 358px; top: 100px; }
  .person-name { font-family: "Roboto Condensed", Arial, sans-serif; font-weight: 700; font-size: 22px; color: var(--brand-blue); line-height: 26px; }
  .person-title { font-size: 15px; color: var(--brand-yellow); line-height: 18px; margin-bottom: 14px; }
  .contact-list { list-style: none; }
  .contact-item { display: flex; align-items: center; gap: 8px; font-size: 14.5px; color: var(--text-gray); line-height: 19px; }
  .contact-icon { width: 14px; height: 14px; flex: none; }

  .footer-bands { position: absolute; left: 0; bottom: 0; width: 100%; height: 12px; display: flex; gap: 2px; }
  .band { flex: 1; border-radius: 12px 12px 0 0; }
  .band-blue { background: var(--band-blue); }
  .band-yellow { background: var(--brand-yellow); }

  .back-wordmark { position: absolute; left: 0; top: 120px; width: 100%; display: flex; justify-content: center; align-items: center; gap: 14px; }
  .back-wordmark .brand-dot { width: 60px; height: 60px; }
  .back-wordmark .brand-name { font-size: 48px; color: var(--band-blue); }

  .tagline { position: absolute; left: 0; top: 275px; width: 100%; text-align: center; font-family: "Ubuntu", Arial, sans-serif; font-weight: 500; font-size: 17.5px; }
  .tagline-blue { color: var(--band-blue); }
  .tagline-yellow { color: var(--brand-yellow); }
</style>
</head>
<body>
  <section class="card card-front">
    <div class="front-wordmark" style="left:71px;top:138px;">
      <span class="brand-dot"></span>
      <span class="brand-name">NetVaultic</span>
    </div>
    <div class="divider"></div>
    <div class="contact-block">
      <h1 class="person-name">TAVIN ORLOWETH</h1>
      <p class="person-title">FOUNDER &amp; CEO</p>
      <ul class="contact-list">
        <li class="contact-item">
          <svg class="contact-icon" viewBox="0 0 14 14"><rect x="3.5" y="0.5" width="7" height="13" rx="1.5" fill="var(--brand-blue)"/><rect x="5" y="2" width="4" height="8.5" fill="#fff"/></svg>
          555 019 2846
        </li>
        <li class="contact-item">
          <svg class="contact-icon" viewBox="0 0 14 14"><rect x="1" y="3" width="12" height="8.5" fill="var(--brand-blue)"/><path d="M1.5 3.5 L7 7.8 L12.5 3.5" stroke="#fff" stroke-width="1.2" fill="none"/></svg>
          tavin@netvaultic.com
        </li>
        <li class="contact-item">
          <svg class="contact-icon" viewBox="0 0 14 14"><circle cx="7" cy="7" r="6.2" fill="var(--brand-blue)"/><ellipse cx="7" cy="7" rx="2.6" ry="6" stroke="#fff" stroke-width="1" fill="none"/><path d="M1 7 H13" stroke="#fff" stroke-width="1"/></svg>
          www.netvaultic.com
        </li>
        <li class="contact-item">
          <svg class="contact-icon" viewBox="0 0 14 14"><circle cx="7" cy="7" r="6.2" fill="var(--brand-blue)"/></svg>
          netvaultic
        </li>
      </ul>
    </div>
    <div class="footer-bands">
      <span class="band band-blue"></span>
      <span class="band band-yellow"></span>
      <span class="band band-blue"></span>
    </div>
  </section>

  <section class="card card-back">
    <div class="back-wordmark">
      <span class="brand-dot"></span>
      <span class="brand-name">NetVaultic</span>
    </div>
    <p class="tagline"><span class="tagline-blue">Cyber Risk Management,</span> <span class="tagline-yellow">Governance &amp; Consulting</span></p>
  </section>
</body>
</html>
```